Fresh, modern, fun business card for pediatric dental practice

Need a business card for fresh, modern, fun pediatric dental practice

Clean look that matches our website's font and colors

We prefer the look of curved corners on business cards

Target Market(s)

parents (mothers) of young children, professionals, mid-high class

Industry/Entity Type

Dental

Contact Information for Business Card

Maplebrook Pediatric Dentistry
482 Quarry Lane
Suite 517
Fernhollow, PA 17599
717.555.0193
www.maplebrookkidsdental.example

Mei-Ran Tsai, DMD
Corinne Walbeck, DMD
(we are working on our email address, but we would like that on the card as well)

Font styles to use
Sans Serif

Requirements
Must have
• All info; we would also like to make cards for individual staff members
• colors from our website and color palatte, attatched
• use same font and design as website for branding
Nice to have
• clean, simple card that has a pop of color
• we would like to see a few designs with our tag line "where smiles get brighter"
• we are not sure if we want to have it on there or not
• we would like to see a few designs incorporating the ribbon graphic on our website where the word WELCOME is

```html
<!DOCTYPE html>
<html lang="en">
<head>
<meta charset="utf-8">
<title>Maplebrook Pediatric Dentistry – Business Card</title>
<link rel="stylesheet" href="https://fonts.googleapis.com/css2?family=Open+Sans:wght@700&family=Didact+Gothic&display=swap">
<style>
  :root {
    --plum: #512a56;
    --plum-light: #5e3263;
    --magenta: #d0308f;
    --sun: #f7b928;
    --rule: #2a5f9a;
    --ink: #3a3a3a;
    --paper: #ffffff;
    --stage: #2b2b2b;
  }
  * { margin: 0; padding: 0; box-sizing: border-box; }
  html, body { width: 1200px; height: 930px; overflow: hidden; }
  body { background: var(--stage); position: relative; font-family: "Didact Gothic", sans-serif; }

  .card {
    position: absolute;
    width: 560px;
    height: 320px;
    border-radius: 20px;
    overflow: hidden;
    box-shadow: 0 14px 30px rgba(0,0,0,.45);
  }

  /* Front */
  .card--front {
    left: 130px; top: 100px;
    background: linear-gradient(135deg, var(--plum-light), var(--plum));
    display: flex; flex-direction: column; align-items: center; justify-content: center;
  }
  .brand {
    font-family: "Open Sans", sans-serif;
    font-weight: 700;
    color: var(--sun);
    line-height: 1;
    display: flex; align-items: center; gap: 16px;
  }
  .brand__dot { border-radius: 50%; background: var(--sun); flex: none; }
  .brand__name { display: flex; flex-direction: column; }
  .brand__word { letter-spacing: .5px; }
  .brand__sub { letter-spacing: 3px; margin-top: 6px; }

  .card--front .brand__dot { width: 54px; height: 54px; }
  .card--front .brand__word { font-size: 66px; }
  .card--front .brand__sub { font-size: 22px; }

  .front__web {
    margin-top: 34px;
    font-family: "Open Sans", sans-serif;
    font-weight: 700;
    font-size: 12px;
    letter-spacing: 1px;
    color: var(--paper);
  }
  .front__web span { color: var(--sun); }

  /* Back */
  .card--back { left: 510px; top: 500px; background: var(--paper); }
  .card--back .brand { position: absolute; left: 40px; top: 34px; }
  .card--back .brand__dot { width: 38px; height: 38px; }
  .card--back .brand__word { font-size: 40px; }
  .card--back .brand__sub { font-size: 15px; letter-spacing: 2px; margin-top: 4px; }

  .address {
    position: absolute; right: 40px; top: 98px;
    text-align: right; font-size: 14px; line-height: 1.35; color: var(--ink);
    font-style: normal;
  }
  .divider {
    position: absolute; left: 40px; top: 162px; width: 460px; height: 1.5px; background: var(--rule);
  }
  .contacts { position: absolute; left: 40px; top: 176px; list-style: none; }
  .contacts li {
    display: flex; align-items: center; gap: 10px;
    font-size: 15px; color: var(--ink); height: 24px;
  }
  .contacts svg { width: 16px; height: 16px; flex: none; }

  .wave { position: absolute; left: 0; bottom: 0; width: 560px; height: 320px; }
</style>
</head>
<body>

<section class="card card--front" aria-label="Card front">
  <div class="brand">
    <span class="brand__dot"></span>
    <div class="brand__name">
      <span class="brand__word">maplebrook</span>
      <span class="brand__sub">pediatric dentistry</span>
    </div>
  </div>
  <p class="front__web">www.<span>maplebrookkidsdental</span>.example</p>
</section>

<section class="card card--back" aria-label="Card back">
  <div class="brand">
    <span class="brand__dot"></span>
    <div class="brand__name">
      <span class="brand__word">maplebrook</span>
      <span class="brand__sub">pediatric dentistry</span>
    </div>
  </div>

  <address class="address">
    Maplebrook Pediatric Dentistry<br>
    482 Quarry Lane<br>
    Suite 517, Fernhollow, PA 17599
  </address>

  <div class="divider"></div>

  <ul class="contacts">
    <li>
      <svg viewBox="0 0 16 16"><circle cx="8" cy="8" r="7" fill="none" stroke="var(--sun)" stroke-width="1.4"/><path d="M5.5 4.5l1.6 1.4-.8 1.2c.6 1.2 1.4 2 2.6 2.6l1.2-.8 1.4 1.6-1 1c-2.8-.4-5.4-3-5.8-5.8z" fill="var(--ink)"/></svg>
      717.555.0193
    </li>
    <li>
      <svg viewBox="0 0 16 16"><circle cx="8" cy="8" r="7" fill="none" stroke="var(--sun)" stroke-width="1.4"/><rect x="4.5" y="5.5" width="7" height="5" fill="none" stroke="var(--ink)" stroke-width="1"/><path d="M4.5 5.5L8 8.3l3.5-2.8" fill="none" stroke="var(--ink)" stroke-width="1"/></svg>
      info@maplebrookkidsdental.example
    </li>
    <li>
      <svg viewBox="0 0 16 16"><circle cx="8" cy="8" r="7" fill="none" stroke="var(--sun)" stroke-width="1.4"/><circle cx="8" cy="8" r="3.6" fill="none" stroke="var(--ink)" stroke-width="1"/><path d="M4.4 8h7.2M8 4.4c-1.6 2.2-1.6 5 0 7.2M8 4.4c1.6 2.2 1.6 5 0 7.2" fill="none" stroke="var(--ink)" stroke-width=".8"/></svg>
      www.maplebrookkidsdental.example
    </li>
  </ul>

  <svg class="wave" viewBox="0 0 560 320" aria-hidden="true">
    <path d="M0 266 C180 286 300 254 390 208 C460 174 510 164 560 160 L560 320 L0 320 Z" fill="var(--sun)"/>
    <path d="M0 276 C180 296 305 266 395 222 C465 188 512 180 560 178 L560 320 L0 320 Z" fill="var(--magenta)"/>
    <path d="M0 298 C190 314 320 286 410 240 C475 208 520 200 560 198 L560 320 L0 320 Z" fill="var(--plum)"/>
  </svg>
</section>

</body>
</html>
```